Tech Company New PowerPoint Design Project

We are an IT Managed services, cloud and cyber security company https://www.travolin.com.au/ Requesting proposals for a PowerPoint deck template that can be used by our sales team when pitching clients, our head office is located in Australa and we do have regional offices in NZ , USA , SRI LANKA and SINGAPORE. and also required to have a proposal/SOW template created too (not sure if this is something that we can include to this proposal) we may need a lot of things done in future but this is where i like to get started for now.. please let m eknow your thoughts and if you have any questions.
Target Market(s)
Enterprise
Industry/Entity Type
Information Technology
Look and feel

```html
<!DOCTYPE html>
<html lang="en">
<head>
<meta charset="utf-8">
<title>Travolin – Sales Deck</title>
<link href="https://fonts.googleapis.com/css2?family=Poppins:wght@300;400;500;600;700&display=swap" rel="stylesheet">
<style>
:root{
  --stage:#1b1b1d;
  --navy:#0c2a55;
  --ink:#16233b;
  --text:#4a5568;
  --brand:#2fb2ec;
  --brand-deep:#1b8fd6;
  --sky:#dff2fc;
  --card:#ffffff;
  --paper:#f3f8fc;
  --badge:#e6ebf0;
}
*{box-sizing:border-box;margin:0;padding:0}
html,body{width:1200px;height:4476px;overflow:hidden;background:var(--stage);font-family:"Poppins",sans-serif;color:var(--ink)}
.deck{position:relative;width:1200px;height:4476px}
.slide{position:absolute;left:100px;width:1000px;height:562px;overflow:hidden;background:var(--paper)}
.s1{top:110px}.s2{top:730px}.s3{top:1350px}.s4{top:1970px}.s5{top:2590px}.s6{top:3210px}.s7{top:3830px}
.brand{position:absolute;font-family:"Poppins",sans-serif;font-weight:400;color:var(--brand);letter-spacing:1px;line-height:1}
.brand-small{left:40px;top:26px;font-size:40px}
.pill{position:absolute;background:var(--brand);color:#fff;font-weight:600;font-size:20px;letter-spacing:1px;display:flex;align-items:center;justify-content:center;border-radius:6px}

/* slide 1 */
.s1 .hero{position:absolute;inset:0;background:radial-gradient(ellipse at 60% 40%,#2c6fb8 0%,#123c78 45%,#071d43 100%)}
.s1 .brand{left:0;right:0;top:70px;text-align:center;font-size:110px}
.s1 h1{position:absolute;left:0;right:0;top:300px;text-align:center;color:#fff;font-size:50px;font-weight:700}
.s1 .intro{position:absolute;left:190px;width:620px;top:400px;text-align:center;color:#dbe7f5;font-size:15px;line-height:1.6}

/* slide 2 */
.s2{background:#fff}
.s2 .photo{position:absolute;left:480px;top:20px;width:520px;height:310px;background:linear-gradient(135deg,#0d2a4a,#1f5f8f 60%,#0a1e36)}
.s2 h2{position:absolute;left:40px;top:150px;font-size:32px;font-weight:700;color:var(--navy)}
.s2 .lead{position:absolute;left:40px;top:200px;width:400px;font-size:12.5px;line-height:1.6;color:var(--text)}
.s2 .points{position:absolute;left:40px;top:345px;width:560px;list-style:none}
.s2 .points li{position:relative;padding-left:32px;margin-bottom:22px;font-size:12.5px;line-height:1.6;color:var(--text)}
.s2 .points li::before{content:"";position:absolute;left:0;top:4px;width:16px;height:16px;border-radius:50%;background:var(--brand)}

/* slide 3 */
.s3{background:#fff}
.s3 .pill{left:270px;top:24px;width:340px;height:46px}
.s3 .band{position:absolute;left:0;right:0;top:90px;height:180px;background:linear-gradient(180deg,#cfe9fa,#6fb7e6 50%,#dff2fc)}
.desk-cards{position:absolute;left:45px;top:230px;width:910px;display:flex;gap:30px}
.desk-card{flex:1;height:300px;background:var(--card);border-radius:10px;box-shadow:0 6px 18px rgba(12,42,85,.15);padding:24px 18px;text-align:center}
.desk-card svg{width:54px;height:54px;margin-bottom:14px}
.desk-card h3{font-size:17px;font-weight:700;line-height:1.25;margin-bottom:12px;color:var(--ink)}
.desk-card p{font-size:12px;line-height:1.55;color:var(--text)}

/* slide 4 */
.s4 h2{position:absolute;left:40px;top:225px;font-size:38px;font-weight:700;color:var(--ink)}
.svc{position:absolute;background:var(--card);border-radius:10px;box-shadow:0 4px 14px rgba(12,42,85,.12);padding:26px 16px 14px;text-align:center}
.svc .ico{position:absolute;left:14px;top:14px;width:34px;height:34px;border-radius:50%;background:var(--brand)}
.svc h3{font-size:15px;font-weight:700;margin-bottom:8px;padding-left:30px}
.svc p{font-size:11px;line-height:1.5;color:var(--text)}
.row-top .svc{top:80px;width:200px;height:190px}
.row-bottom .svc{top:300px;width:210px;height:200px}

/* slide 5 */
.s5 .pill{left:760px;top:60px;width:200px;height:40px;font-size:17px}
.partners{position:absolute;left:60px;top:125px;width:880px;display:grid;grid-template-columns:repeat(5,1fr);gap:20px 40px}
.partner{height:36px;background:var(--badge);border-radius:4px}

/* slide 6 */
.s6 .pill{left:45px;top:220px;width:230px;height:52px}
.office{position:absolute;width:290px;height:200px;background:var(--brand);border-radius:6px;color:#fff;padding:22px 24px}
.office h3{font-size:19px;font-weight:700;margin-bottom:10px;letter-spacing:.5px}
.office p{font-size:11.5px;line-height:1.6}

/* slide 7 */
.s7{background:linear-gradient(160deg,#5fc8f5,#1c9ce5 55%,#1486d0)}
.s7 .brand{left:0;right:0;top:160px;text-align:center;font-size:110px;color:#fff}
.s7 .rule{position:absolute;left:230px;width:540px;top:330px;height:2px;background:#fff}
.s7 .thanks{position:absolute;left:0;right:0;top:350px;text-align:center;color:#fff;font-size:74px;font-weight:300}
</style>
</head>
<body>
<main class="deck">

  <section class="slide s1">
    <div class="hero" role="img" aria-label="Glowing blue digital network of connected points"></div>
    <div class="brand">travolin</div>
    <h1>Welcome to TRAVOLIN</h1>
    <p class="intro">TRAVOLIN is a one-stop destination for all your IT Management Requirements. We are committed to delivering cutting-edge, simplified IT solutions through our highly skilled team and flexible engagement models.</p>
  </section>

  <section class="slide s2">
    <div class="brand brand-small">travolin</div>
    <div class="photo" role="img" aria-label="Hands typing on a laptop with code on screen"></div>
    <h2>ABOUT US</h2>
    <p class="lead">TRAVOLIN is a one-stop destination for all your IT Management Requirements. We are committed to delivering cutting-edge, simplified IT solutions through our highly skilled team and flexible engagement models. Whether you need support for integration or ongoing operational services, TRAVOLIN has the insight and technical capability to deliver simplified solutions.</p>
    <ul class="points">
      <li>Our passion, enthusiasm and values are what make us different from our peers. While there are many businesses providing the same service, what we deliver is unparalleled. Whether services or solutions, we keep standing with our clients through thick and thin.</li>
      <li>Whether you need support for integration or ongoing operational services, TRAVOLIN has the insight and technical capability to deliver simplified solutions.</li>
    </ul>
  </section>

  <section class="slide s3">
    <div class="brand brand-small">travolin</div>
    <div class="pill">MANAGED SERVICE DESK</div>
    <div class="band" role="img" aria-label="Light blue abstract network of connected nodes"></div>
    <div class="desk-cards">
      <article class="desk-card">
        <svg viewBox="0 0 54 54" fill="none" stroke="#1b8fd6" stroke-width="3"><rect x="12" y="8" width="30" height="12" rx="2"/><rect x="12" y="22" width="30" height="12" rx="2"/><rect x="12" y="36" width="30" height="12" rx="2"/><circle cx="36" cy="14" r="1.5" fill="#1b8fd6"/><circle cx="36" cy="28" r="1.5" fill="#1b8fd6"/><circle cx="36" cy="42" r="1.5" fill="#1b8fd6"/></svg>
        <h3>Server &amp; Network Support</h3>
        <p>Address issues and bugs of your server and network devices as a remote service.</p>
      </article>
      <article class="desk-card">
        <svg viewBox="0 0 54 54" fill="none" stroke="#1b8fd6" stroke-width="3"><rect x="8" y="10" width="38" height="26" rx="2"/><path d="M20 46h14M27 36v10"/></svg>
        <h3>Desktop &amp; End User Support</h3>
        <p>Address technical issues and bugs of your desktop environment as well as your users as a remote service.</p>
      </article>
      <article class="desk-card">
        <svg viewBox="0 0 54 54" fill="none" stroke="#1b8fd6" stroke-width="3"><path d="M16 38a9 9 0 0 1 1-18 12 12 0 0 1 23 3 8 8 0 0 1-1 15z"/><path d="M27 30v12M22 37l5 5 5-5"/></svg>
        <h3>Managed Backup &amp; Recovery</h3>
        <p>Provide a data backup and restore service to protect your information and documents against internal accidents, threats, including recovery management.</p>
      </article>
      <article class="desk-card">
        <svg viewBox="0 0 54 54" fill="none" stroke="#1b8fd6" stroke-width="3"><rect x="8" y="10" width="38" height="26" rx="2"/><path d="M13 28l8-8 6 6 10-10M20 46h14M27 36v10"/></svg>
        <h3>Network Monitoring</h3>
        <p>Monitor each device that is connected to network in 24 x 7 and maintain the high level of availability of services.</p>
      </article>
    </div>
  </section>

  <section class="slide s4">
    <div class="brand brand-small">travolin</div>
    <h2>SERVICES</h2>
    <div class="row-top">
      <article class="svc" style="left:320px"><span class="ico"></span><h3>Service Desk</h3><p>Single point of contact for incident and service request handling and remote support including a fixed monthly rate with unlimited support under service level agreements.</p></article>
      <article class="svc" style="left:545px"><span class="ico"></span><h3>Network Operations Center</h3><p>Monitor each device that is connected to network in 24 x 7 and maintain the high level of availability of services.</p></article>
      <article class="svc" style="left:770px"><span class="ico"></span><h3>Procurement Services</h3><p>The procurement team is specialised in sourcing and supplying products and licences to meet the customer's needs.</p></article>
    </div>
    <div class="row-bottom">
      <article class="svc" style="left:30px"><span class="ico"></span><h3>AI as a Service</h3><p>Artificial intelligence tools that reduce the number of hours your business spends on managing your IT operations.</p></article>
      <article class="svc" style="left:270px"><span class="ico"></span><h3>Software Development</h3><p>Design unique software as per your business requirement and provide ongoing support to keep it running smoothly.</p></article>
      <article class="svc" style="left:510px"><span class="ico"></span><h3>Project Services</h3><p>Provide secured and high-quality services for all projects on budget and on time with no delays.</p></article>
      <article class="svc" style="left:750px"><span class="ico"></span><h3>Security Operations Center</h3><p>Our SOC team provides round-the-clock security coverage for organisations to protect their confidentiality, integrity and availability of data.</p></article>
    </div>
  </section>

  <section class="slide s5">
    <div class="brand brand-small">travolin</div>
    <div class="pill">OUR PARTNERS</div>
    <div class="partners" aria-label="Technology partner badges">
      <span class="partner"></span><span class="partner"></span><span class="partner"></span><span class="partner"></span><span class="partner"></span>
      <span class="partner"></span><span class="partner"></span><span class="partner"></span><span class="partner"></span><span class="partner"></span>
      <span class="partner"></span><span class="partner"></span><span class="partner"></span><span class="partner"></span><span class="partner"></span>
      <span class="partner"></span><span class="partner"></span><span class="partner"></span><span class="partner"></span><span class="partner"></span>
      <span class="partner"></span><span class="partner"></span><span class="partner"></span><span class="partner"></span><span class="partner"></span>
      <span class="partner"></span><span class="partner"></span><span class="partner"></span><span class="partner"></span><span class="partner"></span>
      <span class="partner"></span><span class="partner"></span><span class="partner"></span><span class="partner"></span><span class="partner"></span>
    </div>
  </section>

  <section class="slide s6">
    <div class="brand brand-small">travolin</div>
    <div class="pill">LOCATIONS</div>
    <article class="office" style="left:330px;top:110px"><h3>AUSTRALIA</h3><p>TRAVOLIN PTY LTD<br>www.travolin.com.au<br>ABN 00 000 000 000<br>Level 4, 12 Harbour Street<br>Sydney NSW 2000<br>AUSTRALIA</p></article>
    <article class="office" style="left:660px;top:110px"><h3>SRI LANKA</h3><p>TRAVOLIN (PRIVATE) LIMITED<br>PV 00000<br>Floor 3, Lotus Business Centre<br>21 Lake Drive<br>Colombo 03<br>SRI LANKA</p></article>
    <article class="office" style="left:30px;top:320px"><h3>USA</h3><p>TRAVOLIN INC<br>88 Riverside Avenue<br>Suite 210<br>Hartford, CT 06100<br>USA</p></article>
    <article class="office" style="left:345px;top:345px"><h3>NEW ZEALAND</h3><p>TRAVOLIN NZ LIMITED<br>NZBN 0000000000000<br>45 Quay Lane<br>Auckland 1010<br>NEW ZEALAND</p></article>
    <article class="office" style="left:670px;top:345px"><h3>SINGAPORE</h3><p>TRAVOLIN SG PTE LTD<br>UEN 000000000X<br>9 Marina Walk, #05-01<br>Singapore 018900<br>SINGAPORE</p></article>
  </section>

  <section class="slide s7">
    <div class="brand">travolin</div>
    <div class="rule"></div>
    <div class="thanks">Thank You</div>
  </section>

</main>
</body>
</html>
```